Young, dynamic furniture company needs a new business card design

We require a new business card design for our modern furniture company which supplies furniture and appliances to the property and development market.
Oakridge Interiors has become one of the leading furniture & appliance suppliers to the property market withing London. With over 10 years experience, we have increased our business to supply not only private landlords and managing agents, but also property developers, housing associations and local councils.
We offer not only a complete range of furniture which includes beds, wardrobes, dining sets and sofas, but also a high quality, full delivery and assembly service to help you with all our furnishing needs.

Target Market(s)

Private landlords, estate agents, letting agents, property management companies

Industry/Entity Type

Business

Contact Information for Business Card

Name,
Title,
Address,
Mobile,
Telephone,
Fax, Website, email address

Font styles to use
Sans Serif

Colors
3176b5
0555a3
85abd2
cfdeed

Requirements
Must have
• All the above information for each of our staff, along with our logo

```html
<!DOCTYPE html>
<html lang="en">
<head>
<meta charset="utf-8">
<title>Oakridge Interiors – Business Card</title>
<link href="https://fonts.googleapis.com/css2?family=Roboto:wght@300;400;700&display=swap" rel="stylesheet">
<style>
  :root {
    --backdrop: #e9edf2;
    --card: #ffffff;
    --ink: #2b2b2d;
    --ink-soft: #555558;
    --brand: #3176b5;
    --brand-deep: #0555a3;
    --brand-light: #85abd2;
    --brand-pale: #cfdeed;
  }
  * { margin: 0; padding: 0; box-sizing: border-box; }
  html, body {
    width: 1200px; height: 923px; overflow: hidden;
    background: var(--backdrop);
    font-family: "Roboto", Arial, sans-serif;
    color: var(--ink);
  }
  .canvas {
    position: relative; width: 1200px; height: 923px;
  }
  .card {
    position: absolute;
    width: 700px; height: 400px;
    left: 250px;
    background: var(--card);
    border-radius: 26px;
    box-shadow: 0 8px 24px rgba(20, 30, 50, 0.18);
  }
  .card--back { top: 46px; }
  .card--front { top: 477px; }

  /* Brand block */
  .brand { position: absolute; }
  .brand__mark {
    display: flex; align-items: center; gap: 12px;
  }
  .brand__square {
    width: 26px; height: 26px; background: var(--brand-deep);
  }
  .brand__name {
    font-weight: 400; font-size: 30px; letter-spacing: 1px;
    text-transform: uppercase; color: var(--ink);
  }
  .brand__tagline {
    font-weight: 300; font-size: 13px; letter-spacing: 1.2px;
    text-transform: uppercase; color: var(--ink-soft);
    margin-top: 6px; margin-left: 38px;
  }
  .card--back .brand {
    left: 0; right: 0; top: 150px;
    display: flex; flex-direction: column; align-items: center;
  }
  .card--back .brand__tagline { margin-left: 38px; }
  .back__web {
    position: absolute; left: 0; right: 0; top: 290px;
    text-align: center; font-size: 16px; color: var(--ink);
  }
  .card--front .brand { left: 56px; top: 70px; }

  /* Contact block */
  .contact {
    position: absolute; left: 408px; top: 175px;
    padding-left: 22px;
    border-left: 2px solid var(--brand-deep);
  }
  .contact__name {
    font-weight: 700; font-size: 20px; color: var(--brand-deep); line-height: 1.1;
  }
  .contact__title {
    font-size: 15px; color: var(--ink); margin-bottom: 10px;
  }
  .contact__address { font-size: 15px; line-height: 1.35; margin-bottom: 6px; }
  .contact__list { list-style: none; }
  .contact__item {
    display: flex; align-items: center; gap: 8px;
    font-size: 15px; line-height: 1.45;
  }
  .contact__icon { width: 14px; height: 14px; fill: var(--brand-deep); flex: none; }
  .contact__web-name { color: var(--brand-deep); }
</style>
</head>
<body>
<main class="canvas">

  <section class="card card--back" aria-label="Card back">
    <div class="brand">
      <div class="brand__mark">
        <span class="brand__square"></span>
        <span class="brand__name">Oakridge Interiors</span>
      </div>
      <div class="brand__tagline">Trade Furniture Solutions</div>
    </div>
    <p class="back__web">www.oakridgeinteriors.com</p>
  </section>

  <section class="card card--front" aria-label="Card front">
    <div class="brand">
      <div class="brand__mark">
        <span class="brand__square"></span>
        <span class="brand__name">Oakridge Interiors</span>
      </div>
      <div class="brand__tagline">Trade Furniture Solutions</div>
    </div>

    <div class="contact">
      <p class="contact__name">Daniel Reed</p>
      <p class="contact__title">Job Title</p>
      <p class="contact__address">34 Street Name<br>City Name, Country 4567</p>
      <ul class="contact__list">
        <li class="contact__item">
          <svg class="contact__icon" viewBox="0 0 16 16" aria-hidden="true"><path d="M3 1h3l1.5 4-2 1.2a9 9 0 0 0 4.3 4.3L11 8.5l4 1.5v3a2 2 0 0 1-2 2A12 12 0 0 1 1 3a2 2 0 0 1 2-2z"/></svg>
          000 1234 5678
        </li>
        <li class="contact__item">
          <svg class="contact__icon" viewBox="0 0 16 16" aria-hidden="true"><path d="M4 0h8a1 1 0 0 1 1 1v14a1 1 0 0 1-1 1H4a1 1 0 0 1-1-1V1a1 1 0 0 1 1-1zm1 2v10h6V2zm3 11a1 1 0 1 0 0 2 1 1 0 0 0 0-2z"/></svg>
          000 1234 5678
        </li>
        <li class="contact__item">
          <svg class="contact__icon" viewBox="0 0 16 16" aria-hidden="true"><path d="M4 0h8v4H4zM1 5h14a1 1 0 0 1 1 1v6h-3v4H3v-4H0V6a1 1 0 0 1 1-1zm4 6v3h6v-3z"/></svg>
          000 1234 5678
        </li>
        <li class="contact__item">
          <svg class="contact__icon" viewBox="0 0 16 16" aria-hidden="true"><path d="M0 3h16v1L8 9 0 4zm0 2.5 8 5 8-5V13H0z"/></svg>
          info@oakridgeinteriors.com
        </li>
        <li class="contact__item">
          <svg class="contact__icon" viewBox="0 0 16 16" aria-hidden="true"><path d="M8 0a8 8 0 1 0 0 16A8 8 0 0 0 8 0zm0 1.5c.9 0 1.9 2 2.2 5.5H5.8C6.1 3.5 7.1 1.5 8 1.5zM1.6 7h2.7c.1-2 .5-3.7 1.1-4.8A6.5 6.5 0 0 0 1.6 7zm8.9-4.8c.6 1.1 1 2.8 1.1 4.8h2.8a6.5 6.5 0 0 0-3.9-4.8zM1.6 9a6.5 6.5 0 0 0 3.8 4.8c-.6-1.1-1-2.8-1.1-4.8zm4.2 0c.3 3.5 1.3 5.5 2.2 5.5s1.9-2 2.2-5.5zm5.9 0c-.1 2-.5 3.7-1.1 4.8A6.5 6.5 0 0 0 14.4 9z"/></svg>
          <span>www.<span class="contact__web-name">oakridgeinteriors</span>.com</span>
        </li>
      </ul>
    </div>
  </section>

</main>
</body>
</html>
```